VKT Consulting

Government/Entitlement Consulting Services- I assist developers obtain entitlements from local, state and federal government agencies so that they can build their projects. Often these projects are very complicated and political and may face community opposition.

Target Market(s)

Real Estate Developers

Industry/Entity Type

Business Consultant

Contact Information for Business Card

Dana Melbrook
Principal

Font styles to use
Serif
Sans Serif

Requirements
Must have
• Classy and professional appeal.
Nice to have
• I like a combination of a mat and glossy finish. I've seen that done with black and then a bold color for a pop, but am not 100% committed to that.

```html
<!DOCTYPE html>
<html lang="en">
<head>
<meta charset="utf-8">
<title>VKT Consulting – Business Card</title>
<link rel="stylesheet" href="https://fonts.googleapis.com/css2?family=Roboto:wght@300;400;700&display=swap">
<style>
  :root {
    --page-bg: #e9e7e4;
    --card-black: #0d0d0d;
    --card-charcoal: #2f3032;
    --divider: #3a3b3d;
    --accent-white: #f2f2f2;
    --text-light: #d8d8d8;
    --text-soft: #bdbdbd;
  }
  html, body {
    margin: 0;
    padding: 0;
    width: 1200px;
    height: 902px;
    overflow: hidden;
    background: var(--page-bg);
    font-family: "Roboto", Arial, sans-serif;
  }
  .canvas {
    width: 1200px;
    height: 902px;
    display: flex;
    flex-direction: column;
    align-items: center;
    justify-content: center;
    gap: 40px;
  }
  .card {
    width: 700px;
    height: 400px;
    display: block;
    box-shadow: 0 8px 24px rgba(0,0,0,0.25);
  }
  .brand-name { font-family: "Roboto", Arial, sans-serif; font-weight: 700; fill: var(--text-light); }
  .person-name { font-weight: 300; font-size: 34px; fill: var(--text-light); }
  .person-role { font-weight: 300; font-size: 26px; fill: var(--text-soft); }
  .contact-line { font-weight: 400; font-size: 13px; fill: var(--text-light); }
  .contact-icon { fill: var(--text-light); }
</style>
</head>
<body>
<main class="canvas">

  <svg class="card card-back" viewBox="0 0 700 400" xmlns="http://www.w3.org/2000/svg">
    <defs>
      <linearGradient id="backGloss" x1="0" y1="0" x2="1" y2="1">
        <stop offset="0" stop-color="#1a1a1a"/>
        <stop offset="1" stop-color="#050505"/>
      </linearGradient>
    </defs>
    <rect width="700" height="400" fill="url(#backGloss)"/>
    <text class="brand-name" x="350" y="218" font-size="62" text-anchor="middle">VKT Consulting</text>
  </svg>

  <svg class="card card-front" viewBox="0 0 700 400" xmlns="http://www.w3.org/2000/svg">
    <defs>
      <linearGradient id="panelTone" x1="0" y1="0" x2="1" y2="1">
        <stop offset="0" stop-color="#26272a"/>
        <stop offset="1" stop-color="#1a1b1d"/>
      </linearGradient>
      <linearGradient id="rightTone" x1="0" y1="0" x2="1" y2="1">
        <stop offset="0" stop-color="#38393b"/>
        <stop offset="1" stop-color="#2b2c2e"/>
      </linearGradient>
    </defs>
    <rect class="front-base" width="700" height="400" fill="url(#rightTone)"/>

    <g class="textured-panel" role="img" aria-label="Dark panel with fine honeycomb texture">
      <polygon points="0,0 405,0 432,400 0,400" fill="url(#panelTone)"/>
    </g>
    <polygon class="divider-band" points="405,0 418,0 445,400 432,400" fill="var(--divider)"/>
    <polygon class="accent-wedge" points="390,400 432,400 424,318" fill="var(--accent-white)"/>

    <text class="brand-name" x="60" y="118" font-size="40">VKT Consulting</text>

    <text class="person-name" x="650" y="90" text-anchor="end">Dana Melbrook</text>
    <text class="person-role" x="650" y="124" text-anchor="end">Principal</text>

    <g class="contact-list">
      <path class="contact-icon" d="M458 268 q2 -2 4 0 l2.5 2.5 q1 2 -1 3 l-1 1 q2 3.5 5 5 l1 -1 q1 -2 3 -1 l2.5 2.5 q2 2 0 4 l-2 1 q-7 1 -13 -7 q-4 -6 -1 -10z"/>
      <text class="contact-line" x="478" y="280">512-555-0142</text>

      <rect x="458" y="297" width="14" height="10" rx="1" fill="none" stroke="var(--text-light)" stroke-width="1.5"/>
      <rect x="462" y="308" width="6" height="2.5" class="contact-icon"/>
      <text class="contact-line" x="478" y="308">www.vktconsulting.com</text>

      <rect x="458" y="326" width="14" height="10" class="contact-icon"/>
      <path d="M458 326 l7 5.5 l7 -5.5" fill="none" stroke="#2f3032" stroke-width="1.3"/>
      <text class="contact-line" x="478" y="336">info@vktconsulting.com</text>

      <path class="contact-icon" d="M465 351 a5.5 5.5 0 0 1 5.5 5.5 c0 4 -5.5 9 -5.5 9 c0 0 -5.5 -5 -5.5 -9 a5.5 5.5 0 0 1 5.5 -5.5z"/>
      <circle cx="465" cy="356.5" r="1.8" fill="#2f3032"/>
      <text class="contact-line" x="478" y="364" textLength="200" lengthAdjust="spacingAndGlyphs">14 Alder Lane Westbrook NSW 2790</text>
    </g>
  </svg>

</main>
</body>
</html>
```